Briefpapier und Visitenkarten für Bayerisches Gasthaus mit Zimmer
Zielgruppe
Traditionelle Gaststätte im Zentrum einer Kleinstadt in Bayern. Direkt am Marktplatz. 10 Gästezimmer.
Bayerisch. Traditionell. Von junger Geschäftsführerin geführt, mit jungem Personal. Wir haben das Objekt erst vor Kurzem erworben und fangen gerade an.
Gerichte: Braten, Steaks, Brotzeiten, vegetarische und VEGANE Speisen
Getränke: Sehr bierlastig. Es war früher ein Brauereigasthaus. Heute gibts auch eine kleine feine Weinkarte.
Zielgruppe sind Einheimische und Touristen. Im Sommer kommen Radfahrer und Wanderer. Besonders angesprochen werden auch Kinder. Es gibt eine großzügige Spielecke.
Aufgabenstellung
Das Gasthaus heißt Falke. Daher spielt der Falke im Design auch eine wichtige Rolle.
Nachdem wir sehr familienorientiert sind, könnte ich mir auch eine Falke-Familie vorstellen.
Visitenkarten und Briefpapier sollen alle wichtigen Infos enthalten, aber dabei sehr klar gehalten werden und nicht überladen sein. Mir ist ein schlichtes und ansprechendes Design wichtig. Es soll nicht verspielt sein.
Hier ist die Homepage:
www.falke-haldenau-gast.de
Info auf Briefpapier:
GASTHAUS FALKE
Trauber GmbH
Als Info auf Visitenkarte:
Gasthaus Falke

```html
<!DOCTYPE html>
<html lang="de">
<head>
<meta charset="utf-8">
<title>Gasthaus Falke – Geschäftsausstattung</title>
<link href="https://fonts.googleapis.com/css2?family=Jost:wght@300;400;600;700&display=swap" rel="stylesheet">
<style>
  :root{
    --brand-red:#b9102e;
    --brand-dark:#3a3a3c;
    --paper:#ffffff;
    --stage-top:#ffffff;
    --stage-bottom:#f6e7e2;
    --text:#4a4a4a;
    --mark-line:#b8b8b8;
  }
  *{margin:0;padding:0;box-sizing:border-box}
  html,body{width:1200px;height:865px;overflow:hidden}
  body{
    position:relative;
    font-family:"Jost",sans-serif;
    color:var(--text);
    background:linear-gradient(to bottom,var(--stage-top) 0 531px,var(--stage-bottom) 531px 100%);
  }
  .sheet{
    position:absolute;width:490px;height:693px;background:var(--paper);
    box-shadow:0 1px 4px rgba(0,0,0,.18);
  }
  .sheet--back{left:199px;top:141px}
  .sheet--front{left:32px;top:31px}
  .sheet__strip{position:absolute;left:0;width:7px}
  .sheet__strip--dark{top:0;height:93px;background:var(--brand-dark)}
  .sheet__strip--red{top:106px;bottom:0;background:var(--brand-red)}
  .sheet--back .sheet__strip--red{top:0}

  .brand{position:absolute;display:flex;flex-direction:column;align-items:flex-end;gap:10px}
  .brand__dot{border-radius:50%;background:var(--brand-red)}
  .brand__name{font-weight:700;color:var(--brand-red);letter-spacing:.01em;line-height:1;white-space:nowrap}
  .sheet .brand{left:322px;top:20px;width:118px}
  .sheet .brand__dot{width:56px;height:56px}
  .sheet .brand__name{font-size:15.5px}

  .contact{position:absolute;font-weight:300;font-size:8.4px;line-height:10.6px;color:var(--text)}
  .contact__web{font-weight:700;color:var(--brand-red);margin-top:7px}
  .sheet .contact{left:323px;top:127px}

  .sender-line{position:absolute;left:61px;top:108px;font-size:6.2px;font-weight:400;color:#333;white-space:nowrap}
  .sender-line strong{color:var(--brand-red);font-weight:700}
  .window-mark{position:absolute;width:5px;height:5px;border-color:var(--mark-line);border-style:solid;border-width:0}
  .window-mark--tl{left:47px;top:118px;border-left-width:1px;border-top-width:1px}
  .window-mark--tr{left:240px;top:118px;border-right-width:1px;border-top-width:1px}
  .window-mark--bl{left:47px;top:205px;border-left-width:1px;border-bottom-width:1px}
  .window-mark--br{left:240px;top:205px;border-right-width:1px;border-bottom-width:1px}
  .fold-mark{position:absolute;left:7px;width:12px;height:1px;background:var(--mark-line)}

  .footer{position:absolute;left:323px;top:540px;font-weight:300;font-size:8.4px;line-height:10.6px}
  .footer p+p{margin-top:5.5px}

  .hero-brand{position:absolute;left:800px;top:40px;width:295px;display:flex;flex-direction:column;align-items:flex-end;gap:24px}
  .hero-brand .brand__dot{width:150px;height:150px;align-self:center}
  .hero-brand .brand__name{font-size:38px}

  .swatch{position:absolute;width:41px;height:40px}
  .swatch--red{left:811px;top:392px;background:var(--brand-red)}
  .swatch--dark{left:964px;top:392px;background:var(--brand-dark)}
  .swatch-spec{position:absolute;top:392px;font-size:8.4px;line-height:10.5px;color:#222;font-weight:400}
  .swatch-spec--red{left:858px;display:grid;grid-template-columns:24px auto;column-gap:6px}
  .swatch-spec--red span:nth-child(odd){text-align:right}
  .swatch-spec--dark{left:1013px}

  .card{position:absolute;width:230px;height:149px;box-shadow:0 1px 4px rgba(0,0,0,.2)}
  .card--dark{left:928px;top:569px;background:var(--brand-dark)}
  .card--light{left:740px;top:685px;background:var(--paper)}
  .card--dark .brand{left:64px;top:30px;align-items:center;gap:10px}
  .card--dark .brand__dot{width:44px;height:44px;background:#fff}
  .card--dark .brand__name{color:#fff;font-size:14px}
  .card--light .brand{left:110px;top:12px;width:84px;gap:8px}
  .card--light .brand__dot{width:34px;height:34px}
  .card--light .brand__name{font-size:11px}
  .card__person{position:absolute;left:16px;top:64px;line-height:1}
  .card__name{font-size:8px;font-weight:600;color:var(--brand-red)}
  .card__role{font-size:5.4px;font-weight:400;color:var(--text);margin-top:2px}
  .card--light .contact{left:112px;top:89px;font-size:6.6px;line-height:9.6px}
  .card--light .contact__web{margin-top:5px}
  .card__band{position:absolute;left:0;right:0;bottom:0;height:4px;background:var(--brand-dark)}
</style>
</head>
<body>

  <section class="sheet sheet--back" aria-label="Briefbogen Folgeseite">
    <div class="sheet__strip sheet__strip--red"></div>
    <div class="brand">
      <span class="brand__dot"></span>
      <span class="brand__name">GASTHAUS FALKE</span>
    </div>
  </section>

  <section class="sheet sheet--front" aria-label="Briefbogen erste Seite">
    <div class="sheet__strip sheet__strip--dark"></div>
    <div class="sheet__strip sheet__strip--red"></div>

    <div class="brand">
      <span class="brand__dot"></span>
      <span class="brand__name">GASTHAUS FALKE</span>
    </div>

    <address class="contact">
      Lindenplatz 7<br>
      84999 Haldenau<br>
      Telefon: 08731/4460<br>
      info@falke-haldenau-gast.de
      <div class="contact__web">www.falke-haldenau-gast.de</div>
    </address>

    <p class="sender-line">GASTHAUS <strong>FALKE</strong> | Lindenplatz 7 | 84999 Haldenau</p>
    <span class="window-mark window-mark--tl"></span>
    <span class="window-mark window-mark--tr"></span>
    <span class="window-mark window-mark--bl"></span>
    <span class="window-mark window-mark--br"></span>

    <span class="fold-mark" style="top:245px"></span>
    <span class="fold-mark" style="top:347px"></span>
    <span class="fold-mark" style="top:490px"></span>

    <div class="footer">
      <p>GASTHAUS FALKE<br>Trauber GmbH</p>
      <p>Geschäftsführer:<br>Marlene Trauber</p>
      <p>Steuernummer: 123456<br>USt.-IdNr.: DE 123456<br>Handelsregister: Haldenau</p>
      <p>Musterbank Haldenau<br>Kontoinhaber: Trauber GmbH<br>IBAN: DE00998877665544332211<br>BIC: HALDDEF1XXX</p>
    </div>
  </section>

  <div class="hero-brand">
    <span class="brand__dot"></span>
    <span class="brand__name">GASTHAUS FALKE</span>
  </div>

  <span class="swatch swatch--red"></span>
  <div class="swatch-spec swatch-spec--red">
    <span>15%</span><span>Cyan</span>
    <span>100%</span><span>Magenta</span>
    <span>90%</span><span>Yellow</span>
    <span>10%</span><span>Schwarz</span>
  </div>
  <span class="swatch swatch--dark"></span>
  <div class="swatch-spec swatch-spec--dark">90%&nbsp;&nbsp;Schwarz</div>

  <section class="card card--dark" aria-label="Visitenkarte Rückseite">
    <div class="brand">
      <span class="brand__dot"></span>
      <span class="brand__name">GASTHAUS FALKE</span>
    </div>
  </section>

  <section class="card card--light" aria-label="Visitenkarte Vorderseite">
    <div class="card__person">
      <div class="card__name">Marlene Trauber</div>
      <div class="card__role">Geschäftsführerin</div>
    </div>
    <div class="brand">
      <span class="brand__dot"></span>
      <span class="brand__name">GASTHAUS FALKE</span>
    </div>
    <address class="contact">
      Lindenplatz 7<br>
      84999 Haldenau<br>
      Telefon: 08731/4460<br>
      info@falke-haldenau-gast.de
      <div class="contact__web">www.falke-haldenau-gast.de</div>
    </address>
    <div class="card__band"></div>
  </section>

</body>
</html>
```